I want ideas sample designs for my book cover

Hello,

We need a book cover designed in flat and 3D Versions. We would like to have jpg and png for final output and include a copy of the PSD for future revisions.

Here are the basic details:

Title: The Harvest of Quiet Builders
Author: Norman Quillfeather

Dimensions of book:

Was looking at the Pavo website for dimensions. I thought you may want to go on there and look at the different sizes. I used the 6x9” perfect bound US trade size for my book. You will see that this has a spine width of 0.225”, Cover size of 12.48 x 9.25” and spine begins at 6.125”

If you need background info on the author just to get an idea what he does, please check:

http://NormanQuillfeather.example

IMPORTANT: Please see attached document for a more detailed info:

Exact Title Of book
Back Cover
Spine Info
Measurements of book and dimension
Examples of book covers
Norman's photo attached

Thanks,
Darlene

Industry/Entity Type

Life Coaching

Font styles to use
Serif

Requirements
Must have
• Jpg, png and PSD files
• title
• author
• exact dimensions
• front and back cover
• flat and 3d versions

```html
<!DOCTYPE html>
<html lang="en">
<head>
<meta charset="utf-8">
<title>The Harvest of Quiet Builders – Cover Spread</title>
<link href="https://fonts.googleapis.com/css2?family=Anton&family=Source+Sans+3:ital,wght@0,400;0,600;0,700;1,400&display=swap" rel="stylesheet">
<style>
  :root {
    --orange: #f26b21;
    --black: #0b0b0e;
    --ink: #141414;
    --white: #ffffff;
    --sky-top: #a9c8e4;
    --sky-mid: #d6e4ef;
    --sea: #1f4a7a;
    --figure: #0f1420;
  }
  * { box-sizing: border-box; margin: 0; padding: 0; }
  html, body { width: 1200px; height: 893px; overflow: hidden; background: var(--black); }
  .cover {
    position: relative; width: 1200px; height: 893px;
    font-family: "Source Sans 3", sans-serif;
    background: var(--black);
  }
  .back-panel {
    position: absolute; left: 0; top: 0; width: 614px; height: 620px;
    background: var(--orange);
  }
  .blurb {
    position: absolute; left: 50px; top: 60px; width: 505px;
    color: var(--ink); font-size: 12.6px; line-height: 16.8px;
    text-align: justify; hyphens: auto;
  }
  .blurb p + p { margin-top: 16.8px; }
  .spine-title {
    position: absolute; left: 590px; top: 70px;
    writing-mode: vertical-rl;
    font-size: 13.5px; font-weight: 600; letter-spacing: 2.4px;
    color: var(--ink);
  }
  .spine-author {
    position: absolute; left: 592px; top: 702px;
    writing-mode: vertical-rl;
    font-size: 13.5px; color: var(--white);
  }
  .author-photo {
    position: absolute; left: 47px; top: 620px; width: 155px; height: 155px;
    background: linear-gradient(135deg, #e8e8e8, #9a9a9a);
  }
  .author-bio {
    position: absolute; left: 227px; top: 627px; width: 328px;
    color: var(--white); font-size: 10.6px; line-height: 13.6px;
    text-align: justify;
  }
  .author-url {
    position: absolute; left: 72px; top: 806px;
    color: var(--white); font-size: 11px; font-style: italic;
  }
  .isbn-box {
    position: absolute; left: 334px; top: 785px; width: 145px; height: 70px;
    background: var(--white); color: var(--ink);
    font-size: 7.5px; text-align: center; padding-top: 8px;
  }
  .front-photo {
    position: absolute; left: 614px; top: 0; width: 586px; height: 620px;
    background:
      radial-gradient(ellipse 190px 330px at 300px 430px, var(--figure) 0 98%, transparent 100%),
      linear-gradient(180deg, var(--sky-top) 0%, var(--sky-mid) 55%, #7fa2c4 70%, var(--sea) 80%, #2b5e8f 100%);
  }
  .front-kicker {
    position: absolute; left: 614px; width: 586px; top: 32px;
    text-align: center; color: var(--ink); font-size: 21px;
  }
  .front-kicker strong { font-weight: 700; }
  .front-author {
    position: absolute; left: 614px; width: 586px; top: 62px;
    text-align: center; color: var(--orange);
    font-size: 48px; font-weight: 700; letter-spacing: -0.5px;
  }
  .front-tagline {
    position: absolute; left: 740px; width: 330px; top: 418px;
    text-align: center; color: var(--white);
    font-size: 19.5px; line-height: 28.4px;
  }
  .front-title {
    position: absolute; left: 640px; width: 540px; top: 650px;
    text-align: center; color: var(--orange);
    font-family: "Anton", sans-serif; text-transform: uppercase;
  }
  .front-title .line { display: block; font-size: 78px; line-height: 92px; }
  .front-title .article { font-size: 44px; text-transform: none; }
</style>
</head>
<body>
<div class="cover">
  <div class="back-panel"></div>

  <div class="blurb">
    <p>This path goes way beyond Entrepreneurism! This is a book for the awakening Entrepreneurs who are building businesses for a better world, affecting generations to come. Bringing you disruptive (in a good way) information, to turn you and your business inside-out for maximum acceleration towards your organisational vision, mission and values.</p>
    <p>There is the potential to have a more meaningful life and business by discovering the symbiotic relationship that exists between all beings. You will be empowered to take your life and business to the next level if you answer the call in this book. It will introduce you to the power of Amazonian plant medicine and other entheogens for improving relationships with yourself, your partner and your family, friends, business associates and Mother Earth.</p>
    <p>An entheogen is defined as ‘a substance (usually from a plant, but not always) that is consumed in order to alter one’s state of consciousness or to act as a catalyst towards encounters with other states of being.’ Plant medicine has been successfully used in South America for thousands of years. This ancient wisdom is helping billionaires, industry icons and entrepreneurs to be better leaders, awakening to its potential for allowing deep examination of the psyche which has the ability to heal, eliminate fears and create a new level of success both personally and professionally.</p>
    <p>Norman shares his own heart-felt personal experiences and insights gained from working with these substances and the amazing medicine men and women of the Amazon who retain thousands of years of ancient wisdom. He has spent years turning himself inside-out to powerfully transform his own life and business and wants to encourage entrepreneurs to do the same. He believes that if enough people have the opportunity to explore their own consciousness, then together we can make a positive impact on humanity. If you are ready to travel to the fringes and take a journey within, you will discover that you are the missing link you have been looking for. Get ready to expand your consciousness, transform your business and create a new inspiring lifestyle, which will benefit all beings and our beautiful Mother Earth.</p>
  </div>

  <div class="spine-title">The HARVEST OF QUIET BUILDERS</div>
  <div class="spine-author">Norman Quillfeather</div>

  <div class="author-photo" role="img" aria-label="Black and white portrait of the author"></div>
  <p class="author-bio">Norman Quillfeather is an internationally-renowned entrepreneur, speaker, philanthropist, thought leader and best-selling author. Having played the role of transformational coach, facilitator and spoken to over three million people from twelve different countries, he challenges you in his second book to journey deep within yourself to examine the core of your true nature and how it impacts your entrepreneurial journey. Some of the world biggest game changers, social entrepreneurs, internet marketers and consultants have reported that Norman’s golden edge is to integrate “purpose with profits” in a way that brings greater meaning to the work they are doing here in the world.</p>
  <div class="author-url">www.NormanQuillfeather.example</div>
  <div class="isbn-box">ISBN</div>

  <div class="front-photo" role="img" aria-label="Photograph of a man in a dark jacket seen from behind, looking out over the ocean under a bright sky"></div>
  <div class="front-kicker">From the Best Selling Author of “<strong>Wayfinding</strong>”</div>
  <div class="front-author">Norman Quillfeather</div>
  <p class="front-tagline">How this<br>ANCIENT WISDOM<br>is HELPING billionaires, industry icons and entrepreneurs TO BE BETTER LEADERS, increase impact and leave a legacy</p>

  <h1 class="front-title">
    <span class="line"><span class="article">The</span> Harvest of</span>
    <span class="line">Quiet Builders</span>
  </h1>
</div>
</body>
</html>
```